Mattress sale flyer front and back

FLYER SIZE!! front and back!
4.25" X 5.5"
or
10.7cm X 13.9 cm

This flyer needs to show the prices
twin.....$99
full.......$159
queen...$199
king....$299

the phone number........(786)471-3926
the address ..........24315 sw 142st miami fl 33157
if possible a map would be appreciated

possible brands to include.......Dorvin, Kaplets, brule & nasher, quilmdown

ATTACHED IS OUR OLD FLYER WITH OUTDATED INFORMATION, I WOULD LIKE SOMETHING SIMILAR. JUST ADD A LITTLE PRICE LIST AND A MAP

***FRONT AND BACK PLEASE****

```html
<!DOCTYPE html>
<html lang="en">
<head>
<meta charset="utf-8">
<title>Bayside Mattress Outlet – Flyer Front and Back</title>
<link rel="stylesheet" href="https://fonts.googleapis.com/css2?family=Oswald:wght@400;500;600;700&display=swap">
<style>
  :root {
    --yellow: #ece21a;
    --yellow-light: #f3ec45;
    --blue: #1d4b95;
    --blue-dark: #163a78;
    --navy: #0d1f3f;
    --ink: #1a2f66;
    --paper: #ffffff;
    --sheet-edge: #e6e8ea;
    --backdrop: #e3e5e7;
    --mattress-light: #f4f5f7;
    --mattress-mid: #d3d6da;
    --map-land: #e4e1da;
    --map-road: #ffffff;
  }
  * { box-sizing: border-box; margin: 0; padding: 0; }
  html, body { width: 1200px; height: 700px; overflow: hidden; }
  body {
    position: relative;
    background: radial-gradient(ellipse at 50% 40%, #f2f3f4 0%, var(--backdrop) 70%, #d6d8da 100%);
    font-family: "Oswald", sans-serif;
    color: var(--ink);
  }
  .flyer {
    position: absolute;
    top: 148px;
    width: 303px;
    height: 420px;
    background: var(--paper);
    border: 1px solid var(--sheet-edge);
    box-shadow: 0 6px 14px rgba(0,0,0,0.12);
  }
  .flyer--front { left: 320px; }
  .flyer--back { left: 640px; }

  .brand-header {
    position: absolute;
    left: 2px; right: 2px;
    background: var(--yellow);
    display: flex;
    flex-direction: column;
    align-items: center;
    justify-content: center;
    color: var(--blue-dark);
    text-align: center;
    font-weight: 500;
  }
  .flyer--front .brand-header { top: 17px; height: 137px; }
  .flyer--back .brand-header { top: 17px; height: 78px; }
  .brand-name { font-size: 26px; line-height: 1.05; letter-spacing: 0.5px; }
  .brand-name__sub { font-size: 15px; letter-spacing: 6px; }
  .flyer--back .brand-name { font-size: 20px; }
  .flyer--back .brand-name__sub { font-size: 11px; letter-spacing: 5px; }
  .brand-mark { width: 14px; height: 14px; border-radius: 50%; background: var(--blue-dark); margin-bottom: 8px; }
  .flyer--back .brand-mark { width: 10px; height: 10px; margin-bottom: 5px; }

  .band {
    position: absolute;
    left: 2px; right: 2px;
    background: var(--blue);
    color: var(--paper);
    text-align: center;
    font-weight: 500;
  }
  .band--tagline { top: 159px; height: 36px; font-size: 16px; line-height: 36px; letter-spacing: 0.3px; }
  .band--contact { top: 98px; height: 47px; font-size: 27px; line-height: 47px; font-weight: 600; }

  .mattress-photo {
    position: absolute;
    top: 195px; left: 2px; right: 2px; height: 135px;
    background: linear-gradient(180deg, var(--mattress-light) 0%, var(--mattress-mid) 55%, #e6e8eb 100%);
  }
  .price-list {
    position: absolute;
    top: 228px; left: 2px; right: 2px;
    display: grid;
    grid-template-columns: auto auto;
    justify-content: center;
    column-gap: 22px;
    row-gap: 4px;
    font-size: 25px;
    font-weight: 600;
    color: var(--ink);
    text-shadow: 0 0 2px #fff, 0 0 3px #fff, 1px 1px 0 #fff, -1px -1px 0 #fff;
  }

  .brand-row {
    position: absolute;
    top: 330px; left: 2px; right: 2px; height: 57px;
    display: flex;
    justify-content: space-around;
    align-items: center;
    padding: 0 12px;
    font-size: 11px;
    font-weight: 500;
    color: var(--blue-dark);
  }
  .partner { display: flex; align-items: center; gap: 4px; }
  .partner__dot { width: 7px; height: 7px; border-radius: 50%; background: var(--blue-dark); }

  .band--brands-note {
    position: absolute;
    top: 387px; left: 2px; right: 2px; height: 22px;
    background: var(--yellow);
    color: var(--ink);
    font-size: 8px;
    font-weight: 600;
    text-align: center;
    line-height: 22px;
  }

  .map-panel {
    position: absolute;
    top: 145px; left: 2px; right: 2px; height: 122px;
    background: var(--blue);
    padding: 5px 7px;
  }
  .map-area {
    width: 100%; height: 100%;
    background: linear-gradient(135deg, #e9e6df 0%, var(--map-land) 60%, #dcd8cf 100%);
    border: 1px solid #9aa6bb;
    position: relative;
  }

  .contact-block {
    position: absolute;
    top: 267px; left: 2px; right: 2px; height: 82px;
    background: var(--blue);
  }
  .call-tab {
    position: absolute;
    top: 10px; left: 0; width: 123px; height: 24px;
    background: var(--navy);
    color: var(--paper);
    font-size: 14px;
    font-weight: 500;
    line-height: 24px;
    padding-left: 20px;
  }
  .phone-panel {
    position: absolute;
    top: 34px; left: 0; width: 138px; height: 44px;
    background: var(--yellow);
    clip-path: polygon(0 0, 88% 0, 100% 100%, 0 100%);
    color: var(--ink);
    font-size: 17px;
    font-weight: 600;
    line-height: 44px;
    padding-left: 10px;
  }
  .address {
    position: absolute;
    top: 18px; left: 148px; right: 4px;
    color: var(--paper);
    font-size: 13.5px;
    font-weight: 500;
    line-height: 21px;
  }

  .social-strip {
    position: absolute;
    top: 349px; left: 2px; right: 2px; height: 38px;
    background: var(--navy);
    display: flex;
    align-items: center;
    padding: 0 8px;
    gap: 8px;
  }
  .social-names { display: flex; flex-direction: column; gap: 1px; color: var(--paper); font-size: 7px; font-weight: 500; width: 68px; }
  .social-links { display: flex; flex-direction: column; gap: 2px; color: var(--paper); font-size: 5.5px; font-weight: 400; margin-left: 20px; }

  .band--website {
    position: absolute;
    top: 389px; left: 2px; right: 2px; height: 20px;
    background: var(--yellow);
    color: var(--ink);
    font-size: 9px;
    font-weight: 600;
    text-align: center;
    line-height: 20px;
  }
</style>
</head>
<body>

<section class="flyer flyer--front" aria-label="Flyer front">
  <header class="brand-header">
    <span class="brand-mark"></span>
    <span class="brand-name">Bayside Mattress</span>
    <span class="brand-name brand-name__sub">OUTLET</span>
  </header>
  <div class="band band--tagline">LOWEST PRICES. BEST BRANDS.</div>
  <div class="mattress-photo" role="img" aria-label="Close-up of a quilted white mattress top"></div>
  <div class="price-list">
    <span>TWIN - $99</span><span>FULL - $159</span>
    <span>QUEEN - $199</span><span>KING - $299</span>
  </div>
  <div class="brand-row">
    <span class="partner"><span class="partner__dot"></span>Kaplets</span>
    <span class="partner"><span class="partner__dot"></span>Dorvin</span>
    <span class="partner"><span class="partner__dot"></span>Velmora</span>
    <span class="partner"><span class="partner__dot"></span>brule &amp; nasher</span>
  </div>
  <div class="band--brands-note">AND OTHER GREAT BRAND NAMES!</div>
</section>

<section class="flyer flyer--back" aria-label="Flyer back">
  <header class="brand-header">
    <span class="brand-mark"></span>
    <span class="brand-name">Bayside Mattress</span>
    <span class="brand-name brand-name__sub">OUTLET</span>
  </header>
  <div class="band band--contact">CONTACT US NOW!</div>
  <div class="map-panel">
    <div class="map-area" role="img" aria-label="Street map showing the store location"></div>
  </div>
  <div class="contact-block">
    <div class="call-tab">CALL US!</div>
    <div class="phone-panel">(786)471-3926</div>
    <div class="address">24315 SW 142ST,<br>MIAMI, FL 33157, USA</div>
  </div>
  <div class="social-strip">
    <div class="social-names">
      <span>Linkora</span><span>Circlio</span><span>Chirpa</span>
    </div>
    <div class="social-links">
      <span>HTTPS://WWW.LINKORA.COM/BAYSIDEMATTRESSOUTLET</span>
      <span>HTTPS://CIRCLIO.COM/+BAYSIDEMATTRESSOUTLET</span>
      <span>HTTPS://CHIRPA.COM/BAYSIDEMATTRESSOUTLET</span>
    </div>
  </div>
  <div class="band--website">HTTP://WWW.BAYSIDEMATTRESSOUTLET.COM/</div>
</section>

</body>
</html>
```